Commercial construction business needs a great sales brochure!

We are smaller commercial construction company in the Minneapolis, MN market that is looking for a professional sales brochure that can be used to market our services at trade shows or meetings with potential clients. We provide commercial membrane flat roofing, siding and construction services. The final design should communicate trust, growth and safety.

```html
<!DOCTYPE html>
<html lang="en">
<head>
<meta charset="utf-8">
<title>Ridgeline Commercial – Sales Brochure</title>
<link href="https://fonts.googleapis.com/css2?family=EB+Garamond&family=Work+Sans:wght@400;500;600;700&display=swap" rel="stylesheet">
<style>
:root{
  --stage:#b3b3b3;
  --red:#9a1c20;
  --red-deep:#7e1519;
  --charcoal:#2a2a2c;
  --charcoal-soft:#3a3a3d;
  --paper:#f4f4f4;
  --ink:#333;
  --white:#fff;
}
*{box-sizing:border-box;margin:0;padding:0}
html,body{width:988px;height:1200px;overflow:hidden}
body{background:var(--stage);font-family:"Work Sans",Arial,sans-serif;color:var(--ink);position:relative}
.page-label{position:absolute;font-family:"EB Garamond",Georgia,serif;font-size:20px;color:#222;transform:translateX(-50%);white-space:nowrap}
.page{position:absolute;overflow:hidden;box-shadow:0 3px 8px rgba(0,0,0,.25)}
.abs{position:absolute}
.center{text-align:center}
.photo{position:absolute}

/* cover */
.cover{left:131px;top:97px;width:358px;height:463px;background:linear-gradient(160deg,#fafafa,#e4e4e4)}
.cover svg.frame{position:absolute;inset:0}
.brand-square{width:34px;height:34px;background:var(--charcoal);border-top:5px solid var(--red)}
.brand-name{font-weight:700;color:var(--red);font-size:13px;letter-spacing:.2px;white-space:nowrap}
.cover-circle-text{left:191px;top:342px;width:170px;color:var(--white);font-size:10px;line-height:12.8px;letter-spacing:.4px;text-transform:uppercase;white-space:nowrap}
.cover-url{left:191px;top:439px;width:170px;color:#f2d6d6;font-size:8.5px}

/* back */
.back{left:520px;top:97px;width:359px;height:463px;background:var(--charcoal)}
.back-red{left:0;top:0;width:359px;height:233px;background:linear-gradient(120deg,var(--red-deep),var(--red) 55%,#a3282b)}
.back-divider{left:0;top:233px;width:359px;height:5px;background:var(--white)}
.back-lead{left:0;top:30px;width:359px;color:var(--white);font-size:14px;line-height:17.5px}
.section-title{font-weight:400;letter-spacing:1px;text-transform:uppercase}
.rule{height:1px;background:currentColor}
.quote-box{top:142px;width:149px;height:92px;border:1px solid rgba(255,255,255,.75);border-bottom:none;color:var(--white);padding:10px 8px 0}
.quote-box p{font-size:6.7px;line-height:8.4px;text-align:center}
.quote-source{position:absolute;left:7px;bottom:10px;font-size:7.5px;font-weight:500;letter-spacing:.3px;display:flex;align-items:center;gap:6px}
.quote-source b{font-size:18px;color:rgba(255,255,255,.35);font-weight:700;line-height:8px;height:8px}
.contact-icons{left:0;top:293px;width:359px;display:flex;justify-content:center;gap:3px}
.contact-icons span{width:8px;height:8px;border-radius:50%;background:var(--white)}
.contact-lines{left:0;top:311px;width:359px;color:var(--white);font-size:7.8px;line-height:10px;letter-spacing:.3px}

/* page 2 */
.p2{left:133px;top:597px;width:369px;height:501px;background:var(--paper)}
.p2-red{left:0;top:0;width:369px;height:148px;background:linear-gradient(90deg,var(--red-deep),var(--red) 70%,#a12b2e)}
.p2-band{left:0;top:148px;width:369px;height:179px;background:linear-gradient(135deg,#d9d9d9,#ececec 50%,#d4d4d4)}
.about-copy{left:29px;top:58px;width:320px;color:var(--white);font-size:6.8px;line-height:10px}
.about-bold{left:29px;top:101px;width:300px;color:var(--white);font-size:8.3px;line-height:10px;font-weight:700}
.card{background:var(--white);box-shadow:0 2px 5px rgba(0,0,0,.15);text-align:center;padding-top:8px}
.card.dark{background:var(--charcoal-soft);color:var(--white)}
.card h4{font-size:6.6px;font-weight:500;margin-top:4px;line-height:8px}
.card p{font-size:4.4px;line-height:7.6px;margin:6px 9px 0;color:#555}
.card.dark p{color:#ddd}
.card .more{position:absolute;left:0;bottom:0;width:100%;height:11px;background:var(--red);color:var(--white);font-size:4.6px;line-height:11px}
.url-bar{left:0;width:100%;height:18px;color:var(--white);font-size:8px;letter-spacing:1.6px;line-height:18px;text-align:center}

/* page 3 */
.p3{left:502px;top:597px;width:375px;height:501px;background:var(--paper)}
.p3-dark{left:0;top:148px;width:375px;height:239px;background:var(--charcoal)}
.service{width:90px;text-align:center;color:#e8e8e8}
.service .ring{width:32px;height:32px;border-radius:50%;background:var(--white);border:2px solid #8a8a8a;margin:0 auto;display:flex;align-items:center;justify-content:center}
.service .name{font-size:7px;margin-top:9px;letter-spacing:.2px}
.service .btn{width:47px;height:12px;margin:6px auto 0;background:var(--red);border:1px solid #d96b6e;color:var(--white);font-size:5px;line-height:10px}
.partner{width:46px;height:14px;background:#c9c9c9;border-radius:3px}
</style>
</head>
<body>

<div class="page-label" style="left:312px;top:48px">Cover Page</div>
<div class="page-label" style="left:707px;top:48px">Back Page</div>
<div class="page-label" style="left:309px;top:1130px">Page 2</div>
<div class="page-label" style="left:700px;top:1130px">Page 3</div>

<!-- Cover -->
<section class="page cover">
  <div class="photo" role="img" aria-label="Photo of a new brick and siding multi-family apartment building"
       style="inset:0;background:linear-gradient(180deg,#8aa0b4 30%,#7a5a4a 55%,#5d4638 80%,#3f3129);clip-path:polygon(0 240px,245px 128px,358px 205px,358px 463px,0 463px)"></div>
  <svg class="frame" width="358" height="463" viewBox="0 0 358 463" aria-hidden="true">
    <polygon points="358,60 245,118 358,196" fill="#262626"/>
    <polyline points="0,243 245,131 358,208" fill="none" stroke="#ffffff" stroke-width="5"/>
    <polyline points="0,233 245,121 358,198" fill="none" stroke="#9a1c20" stroke-width="8"/>
    <circle cx="290" cy="411" r="122" fill="#e6e6e6"/>
    <circle cx="290" cy="411" r="108" fill="#9a1c20"/>
  </svg>
  <div class="abs" style="left:0;top:22px;width:228px;display:flex;flex-direction:column;align-items:center;gap:14px">
    <div class="brand-square"></div>
    <div class="brand-name">RIDGELINE COMMERCIAL</div>
  </div>
  <p class="abs center cover-circle-text">We are your<br>dependable partner<br>in commercial,<br>multi-family, and<br>residential roofing,<br>siding, and exterior<br>construction</p>
  <p class="abs center cover-url">ridgelinecommercial.com</p>
</section>

<!-- Back -->
<section class="page back">
  <div class="abs back-red"></div>
  <div class="abs back-divider"></div>
  <p class="abs center back-lead">We are your commercial,<br>multi-family, and residential<br>partners.</p>
  <h3 class="abs center section-title" style="left:0;top:108px;width:359px;color:#fff;font-size:13px">Testimonials</h3>
  <div class="abs rule" style="left:157px;top:127px;width:45px;color:#fff"></div>
  <div class="abs quote-box" style="left:27px">
    <p>“Erik came out promptly to give an estimate. He recommended high quality products, gave a good price and completed the project as promised. Overall a great experience.”</p>
    <div class="quote-source"><b>“</b>HOMEPRO REVIEW</div>
  </div>
  <div class="abs quote-box" style="left:183px">
    <p>“The work Erik did was AWESOME. I highly recommend his services, and would definitely use him again. He is extremely professional, turned around the job very quickly, and the finished product looked excellent.”</p>
    <div class="quote-source"><b>“</b>HOMEPRO REVIEW</div>
  </div>
  <h3 class="abs center section-title" style="left:0;top:265px;width:359px;color:#fff;font-size:13px">Contact Us</h3>
  <div class="abs contact-icons"><span></span><span></span><span></span><span></span><span></span></div>
  <div class="abs center contact-lines">
    <p>482 Birchwood Ln Delano, MN 55328</p>
    <p>(612) 555-0147</p>
    <p>info@ridgelinecommercial.com</p>
    <p>ridgelinecommercial.com</p>
    <p>7:00am – 5:00pm</p>
  </div>
  <div class="abs" style="left:0;top:382px;width:359px;display:flex;flex-direction:column;align-items:center;gap:12px">
    <div style="width:32px;height:32px;background:#fff"></div>
    <div class="brand-name" style="color:#fff;font-size:9.5px">RIDGELINE COMMERCIAL</div>
  </div>
</section>

<!-- Page 2 -->
<section class="page p2">
  <div class="abs p2-red"></div>
  <h2 class="abs section-title" style="left:29px;top:22px;color:#fff;font-size:16px">About Us</h2>
  <div class="abs rule" style="left:29px;top:45px;width:312px;color:rgba(255,255,255,.4)"></div>
  <p class="abs about-copy">Do you have a property that is in need of an update? Bring your project ideas to the experts at Ridgeline Commercial when above and beyond is the expectation. We are your commercial, multi-family, and residential partners in construction, maintenance, and repair in Minnesota.</p>
  <p class="abs about-bold">We are your commercial, multi-family, and residential partners in construction, maintenance, and repair in Minnesota<br>call (612) 555-0147.</p>

  <div class="abs p2-band"></div>
  <div class="abs card" style="left:24px;top:182px;width:102px;height:91px">
    <svg width="12" height="10" viewBox="0 0 12 10" aria-hidden="true"><path d="M1 5l3.5 3.5L11 1.5" fill="none" stroke="#333" stroke-width="2"/></svg>
    <h4>Quality Guarantee</h4>
    <p>We deliver quality assurances on all our work, with multiple avenues of communication open to customers at every stage of the project.</p>
    <div class="more">Read More</div>
  </div>
  <div class="abs card dark" style="left:133px;top:174px;width:102px;height:130px">
    <svg width="16" height="16" viewBox="0 0 16 16" aria-hidden="true"><circle cx="8" cy="8" r="8" fill="#9a1c20"/><path d="M5.2 4.2l1.5-.4.9 2-1 .8a5 5 0 0 0 2.8 2.8l.8-1 2 .9-.4 1.5c-3.6.3-6.9-3-6.6-6.6z" fill="#fff"/></svg>
    <h4>24-Hour Emergency<br>Service</h4>
    <p>If you need emergency services or repairs carried out in Minnesota, make Ridgeline Commercial your first call. We deliver excellence in installation, replacement and repair of the key structural elements for your property.</p>
    <div class="more">Read More</div>
  </div>
  <div class="abs card" style="left:241px;top:182px;width:102px;height:94px">
    <svg width="12" height="11" viewBox="0 0 12 11" aria-hidden="true"><path d="M1 4l2.5-3h5L11 4 6 10z M1 4h10 M4 4l2 6 2-6" fill="none" stroke="#333" stroke-width="1"/></svg>
    <h4>Over 10 Years Experience</h4>
    <p>For a decade, we have installed and maintained durable roofing, siding, and windows for residential and commercial properties.</p>
    <div class="more">Read More</div>
  </div>

  <h3 class="abs center section-title" style="left:0;top:337px;width:369px;font-size:13px;color:#333">Work &amp; Projects</h3>
  <div class="abs rule" style="left:160px;top:359px;width:48px;color:#333"></div>
  <div class="photo" role="img" aria-label="Aerial photo of townhome rooftops among trees" style="left:17px;top:370px;width:107px;height:99px;background:linear-gradient(160deg,#7d7466,#5b5650 60%,#6f6a5e)"></div>
  <div class="photo" role="img" aria-label="Aerial photo of a flat membrane commercial roof" style="left:128px;top:371px;width:107px;height:98px;background:linear-gradient(180deg,#8a8c86,#3e4043 40%,#35373a 80%,#7d7f7a)"></div>
  <div class="photo" role="img" aria-label="Photo of a multi-story apartment building under blue sky" style="left:240px;top:372px;width:108px;height:97px;background:linear-gradient(180deg,#2f64b0,#6b8fb8 45%,#8e9a9a 70%,#5e6a6c)"></div>
  <div class="abs url-bar" style="top:483px;background:var(--red)">www.ridgelinecommercial.com</div>
</section>

<!-- Page 3 -->
<section class="page p3">
  <div class="photo" role="img" aria-label="Photo of a two-story suburban house with stone accents and a landscaped front yard" style="left:0;top:0;width:375px;height:148px;background:linear-gradient(180deg,#3f86d6,#8fb6de 35%,#b5a283 60%,#6c7a4b 90%)"></div>
  <svg class="abs" style="left:0;top:0" width="64" height="148" aria-hidden="true"><polygon points="0,0 64,74 0,148" fill="#9a1c20"/></svg>
  <div class="abs p3-dark"></div>
  <h3 class="abs center section-title" style="left:0;top:162px;width:375px;color:#fff;font-size:14px">Our Services</h3>
  <div class="abs rule" style="left:163px;top:187px;width:48px;color:#fff"></div>
  <p class="abs center" style="left:24px;top:199px;width:328px;color:#e4e4e4;font-size:6.8px;line-height:10px">Ridgeline Commercial is your commercial, multi-family, and residential partners in construction, maintenance, and repair in Minnesota.</p>

  <div class="abs service" style="left:42px;top:227px">
    <div class="ring"><svg width="16" height="14" viewBox="0 0 16 14"><path d="M8 1L1 7h2v6h4V9h2v4h4V7h2z" fill="#444"/></svg></div>
    <div class="name">Roofing</div><div class="btn">Read More</div>
  </div>
  <div class="abs service" style="left:136px;top:227px">
    <div class="ring"><svg width="12" height="14" viewBox="0 0 12 14"><rect x="1" y="1" width="10" height="12" fill="none" stroke="#444" stroke-width="1.6"/><path d="M4 4h1M7 4h1M4 7h1M7 7h1M5 13v-3h2v3" stroke="#444" stroke-width="1.4"/></svg></div>
    <div class="name">Siding</div><div class="btn">Read More</div>
  </div>
  <div class="abs service" style="left:234px;top:227px">
    <div class="ring"><svg width="14" height="14" viewBox="0 0 14 14"><path d="M1 2l5-1v5.5H1zM7 1l6-1v6.5H7zM1 7.5h5V13l-5-1zM7 7.5h6V14l-6-1z" fill="#444"/></svg></div>
    <div class="name">Window Installation</div><div class="btn">Read More</div>
  </div>
  <div class="abs service" style="left:42px;top:308px">
    <div class="ring"><svg width="14" height="14" viewBox="0 0 14 14"><path d="M2 13l6-6" stroke="#444" stroke-width="2.4"/><path d="M6 3l3-2 4 4-2 3z" fill="#444"/></svg></div>
    <div class="name">Construction Services</div><div class="btn">Read More</div>
  </div>
  <div class="abs service" style="left:136px;top:308px">
    <div class="ring"><svg width="14" height="14" viewBox="0 0 14 14"><path d="M2 2l10 10M12 2L2 12" stroke="#444" stroke-width="2.4"/></svg></div>
    <div class="name">Repair Services</div><div class="btn">Read More</div>
  </div>
  <div class="abs service" style="left:234px;top:308px">
    <div class="ring"><svg width="10" height="14" viewBox="0 0 10 14"><path d="M6 0L1 8h4l-1 6 5-8H5z" fill="#444"/></svg></div>
    <div class="name">Insurance Restoration</div><div class="btn">Read More</div>
  </div>

  <h3 class="abs center section-title" style="left:0;top:397px;width:375px;font-size:13px;color:#333">Trusted Partners</h3>
  <div class="abs rule" style="left:168px;top:418px;width:40px;color:#333"></div>
  <div class="abs" style="left:14px;top:431px;width:347px;display:flex;justify-content:space-between">
    <div class="partner"></div><div class="partner"></div><div class="partner"></div><div class="partner"></div><div class="partner"></div><div class="partner"></div>
  </div>
  <div class="abs" style="left:14px;top:455px;width:347px;display:flex;justify-content:space-between">
    <div class="partner"></div><div class="partner"></div><div class="partner"></div><div class="partner"></div><div class="partner"></div><div class="partner"></div>
  </div>
  <div class="abs url-bar" style="top:483px;background:var(--charcoal)">www.ridgelinecommercial.com</div>
</section>

</body>
</html>
```